Business card for medical clinic

I need an upmarket, modern medical/health business card for my clinic

Contact Information for Business Card

name, address, email, qr code

```html
<!DOCTYPE html>
<html lang="en">
<head>
<meta charset="utf-8">
<title>Calden Care Clinic – Business Card</title>
<link href="https://fonts.googleapis.com/css2?family=Cinzel:wght@600&family=Arimo:wght@400&display=swap" rel="stylesheet">
<style>
  :root {
    --backdrop: #a2a2a2;
    --card-white: #fbfbfb;
    --brand-blue: #1f78b4;
    --brand-light: #3aa3dc;
    --navy: #0f5585;
    --ink: #4a4a4a;
    --white: #ffffff;
  }
  * { box-sizing: border-box; margin: 0; padding: 0; }
  html, body { width: 1200px; height: 1020px; overflow: hidden; }
  body {
    background: var(--backdrop);
    font-family: "Arimo", Arial, sans-serif;
    position: relative;
  }
  .card {
    position: absolute;
    width: 700px;
    height: 400px;
    border-radius: 3px;
  }
  .card-front {
    left: 110px;
    top: 80px;
    background: var(--card-white);
    border-bottom: 4px solid var(--brand-blue);
  }
  .card-back {
    left: 390px;
    top: 550px;
    background: var(--navy);
    border-bottom: 4px solid var(--brand-blue);
  }
  .person { position: absolute; left: 56px; top: 118px; }
  .person-name {
    font-family: "Cinzel", Georgia, serif;
    font-weight: 600;
    font-size: 30px;
    letter-spacing: 1px;
    color: var(--brand-blue);
    line-height: 1;
  }
  .person-role { font-size: 17px; color: var(--ink); margin-top: 4px; }
  .divider {
    position: absolute;
    left: 56px;
    right: 56px;
    top: 196px;
    height: 1px;
    background: var(--brand-light);
  }
  .contacts { position: absolute; left: 56px; top: 214px; list-style: none; }
  .contacts li {
    display: flex;
    align-items: center;
    gap: 10px;
    font-size: 17px;
    color: var(--ink);
    line-height: 30px;
  }
  .contacts svg { width: 15px; height: 15px; fill: var(--brand-light); flex: none; }
  .address {
    position: absolute;
    right: 56px;
    bottom: 40px;
    text-align: right;
    font-size: 17px;
    color: var(--ink);
    line-height: 24px;
  }
  .brand-name {
    position: absolute;
    font-family: "Arimo", Arial, sans-serif;
    font-weight: 400;
    white-space: nowrap;
    letter-spacing: 1px;
  }
  .card-front .brand-name { right: 56px; top: 62px; font-size: 26px; color: var(--brand-blue); }
  .card-back .brand-name {
    left: 50%; top: 50%; transform: translate(-50%, -50%);
    font-size: 44px; color: var(--white);
  }
</style>
</head>
<body>
  <section class="card card-front">
    <p class="brand-name">Calden Care Clinic</p>
    <div class="person">
      <p class="person-name">Dana Whitfield</p>
      <p class="person-role">Director/Founder</p>
    </div>
    <div class="divider"></div>
    <ul class="contacts">
      <li>
        <svg viewBox="0 0 16 16" aria-hidden="true"><path d="M3 1h3l1.5 4-2 1.3a9 9 0 0 0 4.2 4.2L11 8.5l4 1.5v3a2 2 0 0 1-2 2A12 12 0 0 1 1 3a2 2 0 0 1 2-2z"/></svg>
        05310 482 7716
      </li>
      <li>
        <svg viewBox="0 0 16 16" aria-hidden="true"><path d="M1 3h14v10H1z M2 4l6 5 6-5" stroke="#fff" stroke-width="1"/></svg>
        hello@caldencareclinic.com
      </li>
      <li>
        <svg viewBox="0 0 16 16" aria-hidden="true"><circle cx="8" cy="8" r="7"/><path d="M1 8h14M8 1c-3 3-3 11 0 14M8 1c3 3 3 11 0 14" stroke="#fff" stroke-width="0.9" fill="none"/></svg>
        www.caldencareclinic.com
      </li>
    </ul>
    <p class="address">1870 Harbor Lane<br>Westfield AV 30918</p>
  </section>

  <section class="card card-back">
    <p class="brand-name">Calden Care Clinic</p>
  </section>
</body>
</html>
```